Simple one page Wordpress website

We need a quick turnaround single page wordpress website.
The design needs to be very simple and clean.
We already have some design assets (logos and colours etc) and some draft copy for the page.

We need all the files for us to be able to create a wordpress site. We can do this ourselves and we will host it.

```html
<!DOCTYPE html>
<html lang="en">
<head>
<meta charset="utf-8">
<title>Kestrel Vet</title>
<link rel="stylesheet" href="https://fonts.googleapis.com/css2?family=Roboto:wght@400;500;700&family=Open+Sans:wght@400;600&display=swap">
<style>
:root{
  --blue:#5089bb;
  --green:#8db012;
  --navy:#2b2a48;
  --ink:#222222;
  --grey:#6b6b6b;
  --hero-top:#efefef;
  --hero-bottom:#dedede;
  --white:#ffffff;
}
*{margin:0;padding:0;box-sizing:border-box}
html,body{width:1200px;height:3737px;overflow:hidden;background:var(--white)}
body{font-family:'Roboto',sans-serif;color:var(--ink)}
.page{position:relative;width:1200px;height:3737px;overflow:hidden}
.abs{position:absolute}

.hero-bg{left:0;top:0;width:1200px;height:760px;background:linear-gradient(180deg,var(--hero-top),var(--hero-bottom))}
.hero-wave{left:0;top:600px}
.nav{left:0;top:41px;width:1200px;display:flex;justify-content:center;gap:22px;font-size:13.5px;font-weight:500;letter-spacing:.2px}
.nav a{color:var(--ink);text-decoration:none;position:relative}
.nav a.active{color:var(--green)}
.nav a.active::after{content:"";position:absolute;left:0;right:0;top:22px;height:4px;border-radius:2px;background:var(--navy)}
.brand{left:155px;top:258px;width:420px;font-size:56px;font-weight:500;color:var(--blue);letter-spacing:2px;line-height:64px;white-space:nowrap}
.hero-photo{left:600px;top:112px;width:370px;height:415px;border-radius:185px 185px 0 0;background:linear-gradient(180deg,#e9e2da,#7fa8d6)}
.slide-btn{width:44px;height:44px;border-radius:50%;background:var(--white);display:flex;align-items:center;justify-content:center;box-shadow:0 1px 4px rgba(0,0,0,.08)}

.mission{left:112px;top:525px;width:976px;height:300px;background:var(--blue);border-radius:20px;color:var(--white)}
.mission h2{position:absolute;left:78px;top:98px;font-size:49px;line-height:52px;font-weight:700}
.mission p{position:absolute;left:435px;top:48px;width:490px;font-size:20.5px;line-height:38.5px;font-weight:700}

.section-title{left:0;width:1200px;text-align:center;font-size:50px;font-weight:700;color:var(--ink);line-height:52px}

.cap-card{top:970px;width:474px;height:455px}
.cap-photo{position:absolute;left:0;top:0;width:474px;height:340px;border-radius:18px 18px 0 0}
.cap-note{position:absolute;left:7px;top:338px;width:460px;height:117px;background:var(--green);border-radius:16px;color:var(--white);font-size:15.5px;font-weight:700;line-height:25.5px;text-align:center;display:flex;align-items:center;justify-content:center;padding:0 18px}

.pathway-bg{left:0;top:1490px}
.pathway-photo{left:78px;top:1720px;width:495px;height:495px;border-radius:50%;background:var(--green)}
.pathway-photo span{position:absolute;left:30px;top:30px;width:448px;height:448px;border-radius:50%;background:linear-gradient(160deg,#dfe6ea,#4f86b4 60%,#c9a37a)}
.pathway{left:600px;top:1700px;width:540px;color:var(--white)}
.pathway h2{font-size:34px;line-height:52px;font-weight:700}
.pathway .lead{margin-top:6px;font-size:16px;line-height:25.5px;font-weight:700}
.pathway ul{list-style:none;margin-top:10px}
.pathway li{font-size:16px;line-height:34.5px;display:flex;align-items:center;gap:18px}
.pathway li svg{flex:none}
.pathway .contact{margin-top:10px;font-size:16px;line-height:25.5px;font-weight:700}
.pathway .contact a{color:var(--white)}

.jv-col{top:2565px;width:474px;font-size:13.6px;line-height:25.6px;color:var(--grey);text-align:justify}

.member{top:2907px;width:300px;text-align:center}
.member .avatar{position:relative;margin:0 auto;width:170px;height:172px}
.member .avatar i{position:absolute;left:0;top:0;width:170px;height:170px;border-radius:50%;border-bottom:14px solid var(--green)}
.member .avatar b{position:absolute;left:2px;top:2px;width:166px;height:160px;border-radius:50%}
.member h3{margin-top:14px;font-size:21px;font-weight:500;color:var(--ink)}
.member p{margin-top:8px;font-size:14px;line-height:25.5px;color:var(--grey);padding:0 12px}

.footer-bg{left:0;top:3240px}
.contact-item{top:3492px;width:340px;text-align:center;font-family:'Open Sans',sans-serif}
.contact-item .icon{margin:0 auto;width:55px;height:55px;border-radius:50%;background:var(--green);display:flex;align-items:center;justify-content:center}
.contact-item h4{margin-top:6px;font-size:18px;font-weight:400;color:var(--green)}
.contact-item p{margin-top:6px;font-size:19px;line-height:25px;color:var(--white)}
.copyright{left:0;top:3681px;width:1200px;text-align:center;font-family:'Open Sans',sans-serif;font-size:15px;color:var(--white)}
</style>
</head>
<body>
<div class="page">

  <div class="abs hero-bg"></div>
  <svg class="abs hero-wave" width="1200" height="180" viewBox="0 0 1200 180" aria-hidden="true">
    <path d="M0 145 C220 150 520 170 760 90 C900 40 1000 20 1080 40 C1140 55 1180 45 1200 38 L1200 180 L0 180 Z" fill="#ffffff"/>
  </svg>

  <nav class="abs nav">
    <a class="active" href="#home">HOME</a>
    <a href="#mission">MISSION</a>
    <a href="#capabilities">CAPABILITIES</a>
    <a href="#animal-health">ANIMAL HEALTH</a>
    <a href="#joint-venture">JOINT VENTURE</a>
    <a href="#team">TEAM</a>
    <a href="#contact">CONTACT US</a>
  </nav>

  <div class="abs brand">KESTREL VET</div>
  <div class="abs hero-photo" role="img" aria-label="Smiling veterinarian in blue scrubs holding a small terrier"></div>
  <div class="abs slide-btn" style="left:69px;top:311px"><svg width="10" height="14" viewBox="0 0 10 14"><path d="M7 2 L2 7 L7 12" stroke="#333" stroke-width="1.6" fill="none"/></svg></div>
  <div class="abs slide-btn" style="left:1086px;top:311px"><svg width="10" height="14" viewBox="0 0 10 14"><path d="M3 2 L8 7 L3 12" stroke="#333" stroke-width="1.6" fill="none"/></svg></div>

  <section class="abs mission" id="mission">
    <h2>MISSION<br>STATEMENT</h2>
    <p>Kestrel Vet is deploying a Software as a Service (SaaS) platform to facilitate the efficient collection, transmission, secure storage and anonymised analysis of data integral to animal diagnostics.</p>
  </section>

  <h2 class="abs section-title" id="capabilities" style="top:894px">CAPABILITIES</h2>
  <div class="abs cap-card" style="left:112px">
    <div class="cap-photo" role="img" aria-label="Brown dachshund at a veterinary check-up" style="background:linear-gradient(180deg,#e6e8ec,#b06a38)"></div>
    <div class="cap-note">Originally developed for the human market, the core platform has been deployed in the UK and Ireland and has been used to securely process nearly 3 million cases</div>
  </div>
  <div class="abs cap-card" style="left:614px">
    <div class="cap-photo" role="img" aria-label="Laughing young woman hugging a small black and white dog" style="background:linear-gradient(180deg,#f4b3bc,#e8c39a)"></div>
    <div class="cap-note">The platform has been widely used by leading pharmacies, employers, the national health service and most of the UK's largest private sector laboratories</div>
  </div>

  <svg class="abs pathway-bg" width="1200" height="900" viewBox="0 0 1200 900" aria-hidden="true">
    <path d="M0 60 C120 40 220 110 330 110 C470 110 600 10 720 10 C850 10 930 120 1040 120 C1110 120 1160 80 1200 60 L1200 820 C1120 720 1040 730 960 760 C880 800 820 900 730 895 C600 890 500 740 360 760 C220 780 120 840 0 840 Z" fill="#5089bb"/>
  </svg>
  <div class="abs pathway-photo" role="img" aria-label="Smiling vet with stethoscope beside a pug on an exam table"><span></span></div>
  <section class="abs pathway" id="animal-health">
    <h2>TURNKEY INITIAL VETERINARY DEPLOYMENT – ANIMAL HEALTH AND WELFARE PATHWAY</h2>
    <p class="lead">Kestrel Vet is finalising the design of a bespoke platform to facilitate the collection and processing of data and tests for the Animal Health and Welfare Pathway. Key elements include:</p>
    <ul>
      <li><svg width="14" height="14" viewBox="0 0 14 14"><circle cx="7" cy="7" r="7" fill="#fff"/><path d="M5.5 4 L8.5 7 L5.5 10" stroke="#5089bb" stroke-width="1.8" fill="none"/></svg>Facilitated data collection at the farm by vets</li>
      <li><svg width="14" height="14" viewBox="0 0 14 14"><circle cx="7" cy="7" r="7" fill="#fff"/><path d="M5.5 4 L8.5 7 L5.5 10" stroke="#5089bb" stroke-width="1.8" fill="none"/></svg>Secure and efficient processing of test samples by labs</li>
      <li><svg width="14" height="14" viewBox="0 0 14 14"><circle cx="7" cy="7" r="7" fill="#fff"/><path d="M5.5 4 L8.5 7 L5.5 10" stroke="#5089bb" stroke-width="1.8" fill="none"/></svg>Digital results reporting</li>
      <li><svg width="14" height="14" viewBox="0 0 14 14"><circle cx="7" cy="7" r="7" fill="#fff"/><path d="M5.5 4 L8.5 7 L5.5 10" stroke="#5089bb" stroke-width="1.8" fill="none"/></svg>Invoice support</li>
      <li><svg width="14" height="14" viewBox="0 0 14 14"><circle cx="7" cy="7" r="7" fill="#fff"/><path d="M5.5 4 L8.5 7 L5.5 10" stroke="#5089bb" stroke-width="1.8" fill="none"/></svg>Data analysis reporting</li>
    </ul>
    <p class="contact">Interested parties seeking further information should contact us at <a href="#contact">info@kestrelvet.example</a></p>
  </section>

  <h2 class="abs section-title" id="joint-venture" style="top:2436px">KESTREL VET IS A JOINT<br>VENTURE BETWEEN</h2>
  <p class="abs jv-col" style="left:112px">Fallow Solutions Limited (Fallow), an innovative veterinary-led, close to market sustainable food research organisation. Fallow brings together a team of highly experienced vets representing key opinion leaders within the livestock industry and additional technical support staff through its shareholder practice Elmsworth Veterinary Group, Yorkshire. Elmsworth is a 75 year old six centre veterinary group in North Yorkshire, focusing on livestock and equine. In turn Elmsworth is part of NorthVets, an independent grouping of 40+ Farm and Equine practices across the UK.</p>
  <p class="abs jv-col" style="left:614px">Precision Health Diagnostics Limited (PHD), is a rapidly growing Software as a Service platform provider in the digital health market. PHD deploys its agile and collaborative software development process working in partnership with its clients, using the skills of both parties to build the best solutions as effectively and efficiently as possible. Its clients include some of the country's largest pharmacies, employers and laboratories.</p>

  <h2 class="abs section-title" id="team" style="top:2840px">THE TEAM</h2>
  <svg class="abs" style="left:50px;top:3008px" width="14" height="22" viewBox="0 0 14 22" aria-hidden="true"><path d="M11 2 L3 11 L11 20" stroke="#8db012" stroke-width="2.4" fill="none"/></svg>
  <svg class="abs" style="left:1136px;top:3008px" width="14" height="22" viewBox="0 0 14 22" aria-hidden="true"><path d="M3 2 L11 11 L3 20" stroke="#8db012" stroke-width="2.4" fill="none"/></svg>
  <div class="abs member" style="left:124px">
    <div class="avatar"><i></i><b role="img" aria-label="Portrait of a team member" style="background:linear-gradient(180deg,#9a9a9a,#c7a57c)"></b></div>
    <h3>John Doe</h3>
    <p>Lorem ipsum dolor sit amet, consectetur adipiscing elit, sed do eiusmod tempor incididunt ut labore et</p>
  </div>
  <div class="abs member" style="left:450px">
    <div class="avatar"><i></i><b role="img" aria-label="Portrait of a team member" style="background:linear-gradient(180deg,#d8d8d8,#6e95bf)"></b></div>
    <h3>John Doe</h3>
    <p>Lorem ipsum dolor sit amet, consectetur adipiscing elit, sed do eiusmod tempor incididunt ut labore et</p>
  </div>
  <div class="abs member" style="left:777px">
    <div class="avatar"><i></i><b role="img" aria-label="Portrait of a team member" style="background:linear-gradient(180deg,#7fb6dc,#3d64a3)"></b></div>
    <h3>John Doe</h3>
    <p>Lorem ipsum dolor sit amet, consectetur adipiscing elit, sed do eiusmod tempor incididunt ut labore et</p>
  </div>

  <svg class="abs footer-bg" width="1200" height="497" viewBox="0 0 1200 497" aria-hidden="true">
    <path d="M0 95 C80 170 200 170 300 90 C380 25 460 -10 560 20 C700 60 760 180 900 180 C1020 180 1100 100 1200 80 L1200 497 L0 497 Z" fill="#2b2a48"/>
  </svg>
  <div class="abs contact-item" id="contact" style="left:91px">
    <div class="icon"><svg width="22" height="26" viewBox="0 0 22 26"><path d="M11 24 C5 16 3 12 3 9 A8 8 0 0 1 19 9 C19 12 17 16 11 24 Z" stroke="#fff" stroke-width="1.6" fill="none"/><circle cx="11" cy="9" r="3" stroke="#fff" stroke-width="1.6" fill="none"/></svg></div>
    <h4>Address :</h4>
    <p>123,Lorem ipsum dolor sit<br>amet, consectetur</p>
  </div>
  <div class="abs contact-item" style="left:417px">
    <div class="icon"><svg width="24" height="24" viewBox="0 0 24 24"><path d="M5 3 L9 3 L10.5 8 L8 9.5 C9.3 12.3 11.7 14.7 14.5 16 L16 13.5 L21 15 L21 19 C21 20 20 21 19 21 C10.5 20.5 3.5 13.5 3 5 C3 4 4 3 5 3 Z" stroke="#fff" stroke-width="1.5" fill="none"/></svg></div>
    <h4>Phone :</h4>
    <p>+1 888 888 8888</p>
  </div>
  <div class="abs contact-item" style="left:748px">
    <div class="icon"><svg width="26" height="18" viewBox="0 0 26 18"><rect x="1" y="1" width="24" height="16" rx="1.5" stroke="#fff" stroke-width="1.6" fill="none"/><path d="M1 2 L13 11 L25 2" stroke="#fff" stroke-width="1.6" fill="none"/></svg></div>
    <h4>Email address :</h4>
    <p>info@companyname.com</p>
  </div>
  <p class="abs copyright">© Copyrights 2022 Company name | All Rights Reserved</p>

</div>
</body>
</html>
```